A new updated business card. A good first impression for new customers to our business.

I need something unique. I will attached a picture of our old rubbish cards, and also our current Logo ( I think this needs an update if you have any ideas, its very basic and budget)The best way you will get to see my business is checking our Facebook page, I don't really know what else to say, but anything you want to know, ask away.www.facebook.com/tkwashandseal/

Target Market(s)

Home owners

Industry/Entity Type

Business

Contact Information for Business Card

T&K's Pressure Cleaning & Concrete Sealing
Maya 0492 615 370 maya@tkwashandseal.com
Dylan 0431 528 906 dylan@tkwashandseal.com

FB: www.facebook.com/tkwashandseal/
Website: www.tkwashandseal.net (This is pretty rubbish- we don't really use it)

100% customer satisfaction guaranteed

All aspects of Hi-Pressure Cleaning
Sealing & Re-Sealing
Roof Cleaning
Colour sealing
Decorative coatings

Free no obligation quotes

Requirements
Must have
• NO OBLIGATION FREE quotes
• 100% Customer satisfaction guaranteed
• Can you please add both names, contact details and email address on one card.
• Dylan 0431 528 906
• dylan@tkwashandseal.com
• Maya 0492 615 370
• maya@tkwashandseal.com
• Please change the services:
• Hot/Cold Hi-Pressure Cleaning
• Sealing & Re-Sealing
• Roof Cleaning
• Colour Sealing
• Decorative Coatings
• Concrete Honing
• Thanks
Nice to have
• Something a bit different, something eye catching.l

```html
<!DOCTYPE html>
<html lang="en">
<head>
<meta charset="utf-8">
<title>T&amp;K's Pressure Cleaning &amp; Concrete Sealing – Business Card</title>
<link rel="stylesheet" href="https://fonts.googleapis.com/css2?family=Open+Sans:ital,wght@0,400;0,600;0,700;1,700&display=swap">
<style>
  :root {
    --backdrop: #8f8f8f;
    --card: #f1f1f1;
    --brand-red: #d30c0c;
    --swoosh-grey: #4a4a4a;
    --ink: #222222;
    --ink-soft: #5a5a5a;
    --white: #ffffff;
  }
  html, body {
    margin: 0;
    width: 1105px;
    height: 1200px;
    overflow: hidden;
    background: var(--backdrop);
    font-family: "Open Sans", Arial, sans-serif;
  }
  .canvas {
    position: relative;
    width: 1105px;
    height: 1200px;
  }
  .card {
    position: absolute;
    left: 182px;
    width: 746px;
    height: 426px;
    background: var(--card);
    overflow: hidden;
  }
  .card--front { top: 120px; }
  .card--back  { top: 637px; }

  /* Front */
  .front-shapes {
    position: absolute;
    inset: 0;
    width: 100%;
    height: 100%;
  }
  .front-brand {
    position: absolute;
    left: 0;
    right: 0;
    top: 88px;
    margin: 0 auto;
    width: 260px;
    text-align: center;
    font-weight: 700;
    font-size: 20px;
    line-height: 1.3;
    color: var(--ink);
  }
  .tagline {
    position: absolute;
    left: 0;
    right: 0;
    top: 190px;
    text-align: center;
    font-weight: 700;
    font-style: italic;
    font-size: 20px;
    color: var(--brand-red);
    margin: 0;
  }
  .contact {
    position: absolute;
    top: 282px;
    color: var(--white);
    line-height: 1;
  }
  .contact--left  { left: 30px; text-align: left; }
  .contact--right { right: 29px; text-align: right; }
  .contact__name  { font-size: 25px; font-weight: 600; margin: 0 0 11px; }
  .contact__phone { font-size: 22px; font-weight: 600; margin: 0 0 9px; }
  .contact__line  { font-size: 19.5px; font-weight: 400; margin: 0 0 8px; }

  /* Back */
  .back-brand {
    position: absolute;
    left: 0;
    right: 0;
    top: 92px;
    text-align: center;
    color: var(--ink);
    font-weight: 700;
    margin: 0;
  }
  .back-brand__short { display: block; font-size: 46px; line-height: 1.1; }
  .back-brand__rest  { display: block; font-size: 25px; line-height: 1.45; }
  .services {
    position: absolute;
    left: 0;
    right: 0;
    top: 289px;
    margin: 0;
    padding: 0;
    list-style: none;
    text-align: center;
    font-size: 20.5px;
    line-height: 28px;
    color: var(--ink-soft);
  }
  .services li { display: inline; }
  .services .dot {
    display: inline-block;
    width: 6px;
    height: 6px;
    border-radius: 50%;
    background: var(--brand-red);
    margin: 0 7px 0 5px;
    vertical-align: middle;
  }
  .quotes {
    position: absolute;
    left: 0;
    right: 0;
    top: 362px;
    text-align: center;
    font-weight: 700;
    font-style: italic;
    font-size: 22px;
    color: var(--brand-red);
    margin: 0;
  }
</style>
</head>
<body>
<main class="canvas">

  <section class="card card--front" aria-label="Business card front">
    <svg class="front-shapes" viewBox="0 0 540 308" preserveAspectRatio="none" aria-hidden="true">
      <path class="swoosh" fill="var(--swoosh-grey)"
            d="M0,126 C150,243 430,222 530,60 C540,80 540,100 540,112 Q250,286 0,141 Z"/>
      <path class="red-band" fill="var(--brand-red)" stroke="var(--white)" stroke-width="1.6"
            d="M0,145 Q250,290 540,118 L541,309 L-1,309 Z"/>
    </svg>

    <div class="front-brand">T&amp;K's Pressure Cleaning &amp; Concrete Sealing</div>
    <p class="tagline">100% customer satisfaction guaranteed</p>

    <div class="contact contact--left">
      <p class="contact__name">Dylan</p>
      <p class="contact__phone">0431 528 906</p>
      <p class="contact__line">dylan@tkwashandseal.com</p>
      <p class="contact__line">facebook.com/tkwashandseal</p>
    </div>
    <div class="contact contact--right">
      <p class="contact__name">Maya</p>
      <p class="contact__phone">0492 615 370</p>
      <p class="contact__line">maya@tkwashandseal.com</p>
      <p class="contact__line">www.tkwashandseal.net</p>
    </div>
  </section>

  <section class="card card--back" aria-label="Business card back">
    <h1 class="back-brand">
      <span class="back-brand__short">T&amp;K's</span>
      <span class="back-brand__rest">Pressure Cleaning</span>
      <span class="back-brand__rest">&amp; Concrete Sealing</span>
    </h1>

    <ul class="services">
      <li>Hot/Cold Hi-Pressure Cleaning <span class="dot"></span></li>
      <li>Sealing &amp; Re-Sealing <span class="dot"></span></li>
      <li>Roof Cleaning</li><br>
      <li>Colour Sealing <span class="dot"></span></li>
      <li>Decorative Coatings <span class="dot"></span></li>
      <li>Concrete Honing</li>
    </ul>

    <p class="quotes">Free no obligation quotes</p>
  </section>

</main>
</body>
</html>
```